WordPress webdesign with coding for our company BRISK The Answer

BRISK The Answer is a payrolling company such as Montaval Wages (one of our competitor https://www.montaval-wages.ch/fr/). We need to set up our website in both languages (Fr and Eng). Our logo is enclosed.
we would like something simple explaining what is payrolling in Graph and wording, who we are and a contact page. you can also take some example if needed from our mother company BRISK The Horizon (www.briskthehorizon.ch) or our sister company (www.briskyourstride.ch). we would like to keep the color panel of our logo (ref. Black = PANTONE P Process Black C
Pink = PANTONE P Process Magenta C
Grey = PANTONE 430 C) as the driver of the website.

```html
<!DOCTYPE html>
<html lang="en">
<head>
<meta charset="utf-8">
<title>BRISK The Answer – Payroll</title>
<link href="https://fonts.googleapis.com/css2?family=Montserrat:wght@400;500;600;700;800&display=swap" rel="stylesheet">
<style>
:root{
  --magenta:#c8075f;
  --magenta-deep:#a8044f;
  --blush:#fdeaf4;
  --ink:#161616;
  --text:#3d3d3d;
  --grey:#7c8389;
  --line:#8a8a8a;
  --white:#ffffff;
  --star:#f39a13;
}
*{box-sizing:border-box;margin:0;padding:0}
html,body{width:1200px;height:4310px;overflow:hidden}
body{font-family:'Montserrat',sans-serif;color:var(--ink);background:var(--white);position:relative}
.abs{position:absolute}
section,header,footer{position:absolute;left:0;width:1200px}
.center{text-align:center;left:0;width:1200px}
.eyebrow{font-size:20px;font-weight:500;color:var(--ink);text-decoration:underline;text-decoration-color:var(--magenta);text-underline-offset:7px;text-decoration-thickness:2px}
.section-title{font-size:36px;font-weight:600;letter-spacing:.5px;text-transform:uppercase;line-height:1.15}
.lead{font-size:15px;color:var(--text);line-height:25px}
.btn{background:var(--magenta);color:var(--white);font-size:14px;font-weight:500;display:flex;align-items:center;justify-content:center;gap:6px;text-transform:uppercase}
/* header */
.site-header{top:0;height:94px}
.brand{left:110px;top:14px;font-size:44px;font-weight:800;letter-spacing:1px;color:var(--ink);line-height:1}
.brand-sub{left:112px;top:66px;font-size:12px;letter-spacing:8px;color:var(--ink);font-weight:500}
.nav a{position:absolute;top:36px;font-size:14px;color:var(--ink);text-decoration:none;font-weight:500}
.nav .active{color:var(--magenta);border-bottom:2px solid var(--magenta);padding-bottom:3px}
/* hero */
.hero{top:94px;height:584px;background:linear-gradient(120deg,#d81a72 0%,var(--magenta) 45%,#e14a8c 100%)}
.hero-photo{left:407px;top:35px;width:793px;height:512px;background:linear-gradient(135deg,#e9e5e0 0%,#c9bcb0 45%,#8d6b55 70%,#ddd6ce 100%)}
.hero-card{left:110px;top:117px;width:489px;height:348px;background:var(--white);box-shadow:0 6px 20px rgba(0,0,0,.15)}
.hero-card h1{position:absolute;left:29px;top:36px;font-size:40px;font-weight:500;line-height:46px;text-transform:uppercase}
.hero-card h1 span{color:var(--magenta);font-weight:700}
.hero-card p{position:absolute;left:29px;top:191px;width:440px;font-size:15px;line-height:24px}
.hero-card .btn{position:absolute;left:29px;top:263px;width:154px;height:40px}
/* partners */
.partners{top:678px;height:139px;background:var(--blush)}
.partner{top:50px;display:flex;align-items:center;gap:10px;font-size:28px;font-weight:600;color:#333}
.partner i{display:block;width:34px;height:34px;background:#333}
/* about */
.about{top:817px;height:644px}
.about-frame{left:127px;top:104px;width:417px;height:401px;border:2px solid var(--magenta)}
.about-photo{left:110px;top:83px;width:417px;height:397px;background:radial-gradient(circle at 55% 45%,#2b7da6 0%,#123d5c 55%,#071a2a 100%)}
.about-chart{left:368px;top:450px;width:213px;height:109px;background:var(--white);box-shadow:0 4px 14px rgba(0,0,0,.2)}
.checks li{list-style:none;display:flex;align-items:center;gap:12px;font-size:15px;color:var(--text);height:26px}
.checks i{width:14px;height:14px;background:var(--ink);display:inline-flex;align-items:center;justify-content:center}
/* services */
.services{top:1461px;height:732px;background:var(--blush)}
.svc{top:277px;width:307px;height:370px}
.svc .img{position:absolute;left:0;top:0;width:307px;height:232px}
.svc .box{position:absolute;left:22px;top:175px;width:263px;height:195px;background:var(--white);text-align:center}
.svc .box.hot{background:var(--magenta);color:var(--white)}
.svc h3{font-size:15px;font-weight:600;margin-top:87px}
.svc p{font-size:13px;line-height:19px;margin:8px 18px 0;color:var(--text)}
.svc .hot p{color:#fbe2ee}
.svc svg{position:absolute;left:107px;top:20px}
.arrow{width:54px;height:54px;border:2px solid var(--ink);border-radius:50%;display:flex;align-items:center;justify-content:center;background:transparent}
/* testimonials */
.testimonials{top:2193px;height:736px}
.tcard{top:263px;width:307px;height:306px;border:1.5px solid var(--line);text-align:center}
.avatar{width:80px;height:80px;border-radius:50%;margin:18px auto 0;background:linear-gradient(180deg,#e8e8e8,#b8c2cc)}
.stars{color:var(--star);font-size:19px;letter-spacing:2px;margin-top:6px}
.tcard h4{font-size:21px;font-weight:500;margin-top:4px}
.tcard .role{font-size:14px;color:var(--text);margin-top:2px}
.tcard p{font-size:13px;line-height:22px;color:var(--text);margin:16px 22px 0}
/* why */
.why{top:2929px;height:389px;background:var(--magenta);color:var(--white)}
.why .eyebrow{color:var(--white);text-decoration-color:var(--white)}
.feat{width:202px;height:77px;background:var(--white);color:var(--ink);display:flex;align-items:center;gap:14px;padding-left:22px;font-size:21px;font-weight:500}
/* blog */
.blog{top:3318px;height:762px}
.post{top:281px;width:305px}
.post .img{width:305px;height:201px}
.post h3{font-size:17px;font-weight:600;line-height:25px;margin-top:12px}
.post .date{font-size:13px;color:var(--text);margin-top:5px}
.post p{font-size:13px;line-height:21px;color:var(--text);margin-top:8px}
.post a{display:block;margin-top:12px;font-size:14px;color:var(--magenta);text-decoration:underline;text-underline-offset:3px}
/* footer */
.site-footer{top:4080px;height:230px;background:var(--blush)}
.foot-nav a{position:absolute;top:151px;font-size:14px;color:var(--ink);text-decoration:none;font-weight:500}
.foot-line{left:0;top:182px;width:1200px;height:1px;background:var(--magenta)}
</style>
</head>
<body>

<header class="site-header">
  <div class="abs brand">BRISK</div>
  <div class="abs brand-sub">THE ANSWER</div>
  <nav class="nav">
    <a class="active" style="left:434px">HOME</a>
    <a style="left:510px">ABOUT US</a>
    <a style="left:614px">SERVICES</a>
    <a style="left:714px">FAQ</a>
    <a style="left:772px">CONTACT</a>
    <a style="left:869px">EN &#8964;</a>
  </nav>
  <div class="abs btn" style="left:934px;top:27px;width:154px;height:40px">&raquo; GET IN TOUCH</div>
</header>

<section class="hero">
  <div class="abs hero-photo" role="img" aria-label="Woman at a desk reviewing payroll papers"></div>
  <div class="abs hero-card">
    <h1>BRISK Services<br>to evolve your<br><span>Payroll</span></h1>
    <p>Lorem ipsum dolor sit amet, consectetur adipiscing elit, sed do eiusmod tempor incididunt</p>
    <div class="btn">&raquo; GET IN TOUCH</div>
  </div>
</section>

<section class="partners">
  <div class="abs partner" style="left:110px"><i style="border-radius:50%"></i>Nordvale</div>
  <div class="abs partner" style="left:382px;font-weight:500">Quarrix</div>
  <div class="abs partner" style="left:650px;font-weight:500">Halden</div>
  <div class="abs partner" style="left:898px"><i></i>Verano</div>
</section>

<section class="about">
  <div class="abs about-frame"></div>
  <div class="abs about-photo" role="img" aria-label="Hand touching a glowing payroll interface with finance icons"></div>
  <div class="abs about-chart">
    <svg width="213" height="109" viewBox="0 0 213 109">
      <polyline points="22,88 48,62 70,78 96,46 120,64 150,30 188,14" fill="none" stroke="#1f6fd1" stroke-width="7" stroke-linejoin="round"/>
      <polyline points="40,92 70,74 98,84 130,60 160,52 190,36" fill="none" stroke="#6bbf7a" stroke-width="3"/>
    </svg>
  </div>
  <div class="abs eyebrow" style="left:624px;top:80px">About Brisk</div>
  <h2 class="abs section-title" style="left:624px;top:135px">Your trusted payroll<br>partner</h2>
  <p class="abs lead" style="left:624px;top:232px;width:460px">BRISK The Answer is part of the BRISK group, providing flexible, secure, and simple payrolling solutions for professionals and companies. Our mission is to take care of administrative burdens so you can focus on your core business.</p>
  <div class="abs btn" style="left:624px;top:375px;width:154px;height:38px">&raquo; READ MORE</div>
  <ul class="abs checks" style="left:624px;top:435px">
    <li><i><svg width="10" height="10" viewBox="0 0 10 10"><path d="M1 5l3 3 5-6" stroke="#fff" stroke-width="2" fill="none"/></svg></i>Lorem Ipsum Dolor Sit Amet, Consectetur Adip</li>
    <li><i><svg width="10" height="10" viewBox="0 0 10 10"><path d="M1 5l3 3 5-6" stroke="#fff" stroke-width="2" fill="none"/></svg></i>Excepteur Sint Occaecat Cupidatat</li>
    <li><i><svg width="10" height="10" viewBox="0 0 10 10"><path d="M1 5l3 3 5-6" stroke="#fff" stroke-width="2" fill="none"/></svg></i>Neque Porro Quisquam Est, Qui Dolor</li>
  </ul>
</section>

<section class="services">
  <div class="abs center"><span class="eyebrow" style="position:relative;top:83px">Our Services</span></div>
  <h2 class="abs center section-title" style="top:139px">Payrolling made simple</h2>
  <p class="abs center lead" style="top:193px;font-size:15px">We manage the administrative, legal, and financial aspects of your work so you<br>can focus on delivering value to your clients.</p>

  <div class="abs arrow" style="left:42px;top:365px"><svg width="16" height="16" viewBox="0 0 16 16"><path d="M11 2L5 8l6 6" stroke="#161616" stroke-width="2" fill="none"/></svg></div>
  <div class="abs arrow" style="left:1104px;top:365px"><svg width="16" height="16" viewBox="0 0 16 16"><path d="M5 2l6 6-6 6" stroke="#161616" stroke-width="2" fill="none"/></svg></div>

  <div class="abs svc" style="left:110px">
    <div class="img" role="img" aria-label="Business people reviewing payroll reports on a tablet" style="background:linear-gradient(135deg,#3b4a5c,#9aa8b8 60%,#e4e8ee)"></div>
    <div class="box">
      <svg width="50" height="50" viewBox="0 0 50 50"><circle cx="25" cy="25" r="16" fill="none" stroke="#c8075f" stroke-width="8" stroke-dasharray="7 5"/><circle cx="25" cy="25" r="12" fill="#c8075f"/><circle cx="25" cy="21" r="4" fill="#fff"/><path d="M17 32c2-5 14-5 16 0" fill="#fff"/></svg>
      <h3>Employment Administration</h3>
      <p>Lorem ipsum dolor sit amet, consectetur adipiscing elit, sed do eiusmod tempor incidid</p>
    </div>
  </div>
  <div class="abs svc" style="left:447px">
    <div class="img" role="img" aria-label="Hand signing an invoice with a pen" style="background:linear-gradient(135deg,#2a2622,#8a8178 55%,#e2dfdb)"></div>
    <div class="box hot">
      <svg width="50" height="50" viewBox="0 0 50 50"><rect x="12" y="6" width="24" height="34" rx="2" fill="none" stroke="#fff" stroke-width="3"/><path d="M17 15h14M17 21h10M17 27h8" stroke="#fff" stroke-width="2.5"/><circle cx="35" cy="34" r="8" fill="#c8075f" stroke="#fff" stroke-width="3"/></svg>
      <h3>Client Invoicing</h3>
      <p>Lorem ipsum dolor sit amet, consectetur adipiscing elit, sed do eiusmod tempor incidid</p>
    </div>
  </div>
  <div class="abs svc" style="left:783px">
    <div class="img" role="img" aria-label="Young man working on a laptop" style="background:linear-gradient(135deg,#e9e2d6,#b07a45 50%,#4a3a2e)"></div>
    <div class="box">
      <svg width="50" height="50" viewBox="0 0 50 50"><path d="M12 14l20-8 3 8" fill="#c8075f"/><rect x="8" y="14" width="34" height="26" rx="3" fill="#c8075f"/><rect x="30" y="23" width="12" height="8" rx="2" fill="#fff"/></svg>
      <h3>Salary Payment</h3>
      <p>Lorem ipsum dolor sit amet, consectetur adipiscing elit, sed do eiusmod tempor incidid</p>
    </div>
  </div>
</section>

<section class="testimonials">
  <div class="abs center"><span class="eyebrow" style="position:relative;top:83px">Our Testimonials</span></div>
  <h2 class="abs center section-title" style="top:139px">Customers share the love</h2>
  <p class="abs center lead" style="top:193px">Real customers share their genuine experiences and how our service made a lasting difference.</p>

  <div class="abs tcard" style="left:110px">
    <div class="avatar" role="img" aria-label="Portrait of client"></div>
    <div class="stars">★★★★★</div>
    <h4>Lionel Ferraz</h4>
    <div class="role">Executive</div>
    <p>Lorem ipsum dolor sit amet, consectetur adipiscing el sed do eiusmod tempor inciunt ut labore et dolore magna aliqua.</p>
  </div>
  <div class="abs tcard" style="left:447px">
    <div class="avatar" role="img" aria-label="Portrait of client"></div>
    <div class="stars">★★★★★</div>
    <h4>Nadia Keller</h4>
    <div class="role">Executive</div>
    <p>Lorem ipsum dolor sit amet, consectetur adipiscing el sed do eiusmod tempor inciunt ut labore et dolore magna aliqua.</p>
  </div>
  <div class="abs tcard" style="left:783px">
    <div class="avatar" role="img" aria-label="Portrait of client"></div>
    <div class="stars">★★★★★</div>
    <h4>Tobias Lindqvist</h4>
    <div class="role">Executive</div>
    <p>Lorem ipsum dolor sit amet, consectetur adipiscing el sed do eiusmod tempor inciunt ut labore et dolore magna aliqua.</p>
  </div>

  <div class="abs arrow" style="left:534px;top:596px"><svg width="16" height="16" viewBox="0 0 16 16"><path d="M11 2L5 8l6 6" stroke="#161616" stroke-width="2" fill="none"/></svg></div>
  <div class="abs arrow" style="left:611px;top:596px"><svg width="16" height="16" viewBox="0 0 16 16"><path d="M5 2l6 6-6 6" stroke="#161616" stroke-width="2" fill="none"/></svg></div>
</section>

<section class="why">
  <div class="abs eyebrow" style="left:112px;top:81px">Why Choose Us</div>
  <h2 class="abs section-title" style="left:112px;top:138px;line-height:42px">We make<br>payroll easy</h2>
  <p class="abs lead" style="left:112px;top:232px;width:520px;color:#fbe2ee">Lorem ipsum dolor sit amet, consectetur adipiscing elit, sed do eiusmod tempor incididunt ut labore et dolore magna aliqua. Ut enim ad minim veniam, quis nostrud exercitatio</p>

  <div class="abs feat" style="left:655px;top:106px"><svg width="40" height="40" viewBox="0 0 40 40"><path d="M20 4l8 8h-5v8h-6v-8h-5z M6 22h12v14H6z M22 26h12v10H22z" fill="none" stroke="#c8075f" stroke-width="2"/></svg>Flexibility</div>
  <div class="abs feat" style="left:886px;top:106px"><svg width="40" height="40" viewBox="0 0 40 40"><path d="M20 3l14 6v10c0 9-6 15-14 18C12 34 6 28 6 19V9z" fill="none" stroke="#c8075f" stroke-width="2"/><rect x="14" y="18" width="12" height="10" fill="none" stroke="#c8075f" stroke-width="2"/><path d="M16 18v-3a4 4 0 018 0v3" fill="none" stroke="#c8075f" stroke-width="2"/></svg>Security</div>
  <div class="abs feat" style="left:655px;top:208px"><svg width="40" height="40" viewBox="0 0 40 40"><circle cx="16" cy="14" r="9" fill="none" stroke="#c8075f" stroke-width="2"/><path d="M16 14l3 16 4-5 6 8 3-2-6-8 6-2z" fill="none" stroke="#c8075f" stroke-width="2"/></svg>Simplicity</div>
  <div class="abs feat" style="left:886px;top:208px"><svg width="40" height="40" viewBox="0 0 40 40"><circle cx="20" cy="10" r="6" fill="none" stroke="#c8075f" stroke-width="2"/><path d="M10 28c0-8 20-8 20 0" fill="none" stroke="#c8075f" stroke-width="2"/><path d="M6 34l2-4 2 4M18 36l2-4 2 4M30 34l2-4 2 4" stroke="#c8075f" stroke-width="2" fill="none"/></svg>Expertise</div>
</section>

<section class="blog">
  <div class="abs center"><span class="eyebrow" style="position:relative;top:83px">Our Blog</span></div>
  <h2 class="abs center section-title" style="top:139px">Latest blog &amp; articles</h2>
  <p class="abs center lead" style="top:192px">Lorem ipsum dolor sit amet, consectetur adipiscing elit, sed do eiusmod tempor<br>incididunt ut labore et dolore magna aliqua</p>

  <article class="abs post" style="left:110px">
    <div class="img" role="img" aria-label="Hands using a calculator over financial documents" style="background:linear-gradient(135deg,#222,#6b6560 55%,#d8d4cf)"></div>
    <h3>Lorem ipsum dolor sit amet, consectetur adipiscing elit, sed do</h3>
    <div class="date">November 25, 2021</div>
    <p>Lorem ipsum dolor sit amet, consect adipiscing elit, sed do eiusmod tempor incid idunt ut labore et dolore magna...</p>
    <a>&raquo; READ MORE</a>
  </article>
  <article class="abs post" style="left:447px">
    <div class="img" role="img" aria-label="Laptop showing a salary spreadsheet" style="background:linear-gradient(135deg,#1b2a3c,#4f6a8a 55%,#c5d0dc)"></div>
    <h3>Lorem ipsum dolor sit amet, consectetur adipiscing elit, sed do</h3>
    <div class="date">November 25, 2021</div>
    <p>Lorem ipsum dolor sit amet, consect adipiscing elit, sed do eiusmod tempor incid idunt ut labore et dolore magna...</p>
    <a>&raquo; READ MORE</a>
  </article>
  <article class="abs post" style="left:783px">
    <div class="img" role="img" aria-label="Man working at a computer in an office" style="background:linear-gradient(135deg,#dcdcdc,#8f8f8f 50%,#2e2e2e)"></div>
    <h3>Lorem ipsum dolor sit amet, consectetur adipiscing elit, sed do</h3>
    <div class="date">November 25, 2021</div>
    <p>Lorem ipsum dolor sit amet, consect adipiscing elit, sed do eiusmod tempor incid idunt ut labore et dolore magna...</p>
    <a>&raquo; READ MORE</a>
  </article>
</section>

<footer class="site-footer">
  <div class="abs center" style="top:56px;font-size:58px;font-weight:800;letter-spacing:2px;line-height:1">BRISK</div>
  <div class="abs center" style="top:120px;font-size:14px;letter-spacing:10px;font-weight:500">THE ANSWER</div>
  <nav class="foot-nav">
    <a style="left:360px">HOME</a>
    <a style="left:449px">ABOUT US</a>
    <a style="left:572px">SERVICES</a>
    <a style="left:691px">FAQ</a>
    <a style="left:768px">CONTACT</a>
  </nav>
  <div class="abs foot-line"></div>
  <div class="abs center" style="top:196px;font-size:14px">Copyright © 2025 BRISK The Answer. All rights reserved.</div>
</footer>

</body>
</html>
```